Home page design for Drone video business (the Business focusses on home videos for realtors)

Dear reader,

*I NEED DESIGNS OF ALL THE PAGES*
We need a first design of a homepage and of 4 other pages of the website of a business that sells drone video services. All the pages will need to be in the similar design style.
The video's are targeted at consumers that want to sell there home and would like to have a cool drone video of photos of their home.

How does the website look:
- has a navbar on top
- A cool looking banner of an areal drone.
- A Big header: with company name: SkyLoftReels
- A smaller subheader: We film your home to increase your chances of sale
- Then a section with a Big header: How does it work
- In this section a place for a vimeo explainitory video
- Then a similar navbar styled bar with a phone number and a email address
- Then a section where the videos porfolio is displayed in a cool way
- Inside this sectiona header: Our work

- A section with header: Why us?
- 4 symbols here with a subheader and some lorum ipsum text underneath (see wireframe images)

- Under that a: Contact us
- where you can put in name, email, phone, message box and a send button

- At the bottom a footer with phone number and a fake address for now.

Be creative. Use creative but serious color.
Use a serious font. Make it a sharp design. Sharp lines. Not to dark design and not to light design.

The wireframes are the same kind of images.
PLEASE PUT IN DESIGNS OF ALL THE PAGES

Good luck

Target Market(s)

People that want to sell home and want to make a cool drone video or photos of their home.

Industry/Entity Type

Business

Contact Information for Business Card

Lucas Wenning
lucas@skyloftreels.example
+31647208351

Logo Text

SkyLoftReels

Number of Pages Required

1 page

Font styles to use
Sans Serif

Requirements
Must have
• All the sections as explained in the instructions.
• The nav bar should have an about us, services, portfolio and a contact us buttons.
• See instruction for details.
• Must include designs of the front page, contact us, our services, portfolio and contact us.
• If you do add some designs for the "about us", "services", "prices", "portfolio" and "contact us" pages, you make a way better chance of winning the competition.
Nice to have
• designs for the other pages as described at the Must haves. You make a better chance of winning if you include them. Look at the wireframes to see the mockups for those pages. think creative about what kind of sections and design should be included in those pages.
Should not have
• bad designs.

```html
<!DOCTYPE html>
<html lang="en">
<head>
<meta charset="utf-8">
<title>SkyLoftReels – Home</title>
<link rel="stylesheet" href="https://fonts.googleapis.com/css2?family=Montserrat:wght@400;500;600;700&family=Open+Sans:ital,wght@0,400;0,600;1,400&display=swap">
<style>
:root{
  --orange:#f05a22;
  --ink:#2b2b2b;
  --text:#555;
  --light:#f3f6f8;
  --grey:#efefef;
  --dark:#2b2b31;
  --darker:#1f1f24;
  --line:#d7dce0;
  --player:#141414;
  --blue:#1aa3e8;
}
*{box-sizing:border-box;margin:0;padding:0}
html,body{width:1200px;height:2456px;overflow:hidden}
body{position:relative;background:#fff;font-family:"Open Sans",Arial,sans-serif;color:var(--ink)}
.section{position:absolute;left:0;width:1200px}
.section-title{position:absolute;left:0;width:100%;text-align:center;font-family:"Montserrat",Arial,sans-serif;font-weight:500;font-size:18px;color:var(--ink)}

/* nav */
.topbar{top:0;height:90px;background:var(--light);border-top:5px solid var(--orange)}
.brand{position:absolute;font-family:"Montserrat",Arial,sans-serif;font-weight:600;font-size:16px;color:var(--orange)}
.topbar .brand{left:123px;top:32px}
.nav{position:absolute;right:123px;top:31px;display:flex;align-items:center;font-family:"Montserrat",Arial,sans-serif;font-size:14px;color:var(--ink)}
.nav a{color:inherit;text-decoration:none;padding-bottom:8px}
.nav a.active{color:var(--orange);border-bottom:2px solid var(--orange)}
.nav .sep{margin:0 19px;padding-bottom:8px;font-size:13px}

/* hero */
.hero{top:90px;height:417px;background:linear-gradient(180deg,#5d97cf 0%,#9fc3e6 35%,#dfe9f0 70%,#9cab45 88%,#6f8a2e 100%);overflow:hidden}
.hero-photo{position:absolute;left:600px;top:60px;width:460px;height:270px;background:radial-gradient(ellipse at center,rgba(255,255,255,.85) 0%,rgba(230,235,238,.5) 45%,rgba(255,255,255,0) 70%)}
.hero h1{position:absolute;left:123px;top:160px;font-family:"Montserrat",Arial,sans-serif;font-weight:700;font-size:28px;color:#1d1d1d}
.hero p{position:absolute;left:123px;top:196px;width:420px;font-family:"Montserrat",Arial,sans-serif;font-size:21px;line-height:26px;color:#2a2a2a}
.btn{position:absolute;background:var(--orange);color:#fff;font-family:"Montserrat",Arial,sans-serif;font-weight:600;text-align:center;text-transform:uppercase}
.hero .btn{left:123px;top:259px;width:114px;height:39px;line-height:39px;font-size:13px}
.hero-tab{position:absolute;left:512px;top:385px;width:177px;height:90px;border-radius:89px 89px 0 0;background:var(--orange)}
.dots{position:absolute;left:568px;top:398px;display:flex;gap:5px}
.dots span{width:7px;height:7px;border:1.5px solid #fff}
.dots span:first-child{background:#fff}

/* how it works */
.how{top:507px;height:420px;background:#2d2f31;overflow:hidden}
.how-photo{position:absolute;left:0;top:0;width:1200px;height:420px;background:linear-gradient(90deg,#3c3d3e 0%,#2a2b2c 40%,#303233 70%,#3d4142 100%)}
.how .section-title{top:27px;color:#fff}
.player{position:absolute;left:368px;top:81px;width:467px;height:260px;background:var(--player);border:1px solid #000}
.player-thumb{position:absolute;left:8px;top:8px;width:48px;height:48px;background:linear-gradient(135deg,#3b5f8a,#c75a3a)}
.player-title{position:absolute;left:66px;top:10px;font-family:"Montserrat",Arial,sans-serif;font-weight:700;font-size:14px;color:var(--blue)}
.player-by{position:absolute;left:66px;top:30px;font-size:10px;color:#fff}
.player-by span{color:var(--blue)}
.player-side{position:absolute;right:10px;top:10px;display:flex;flex-direction:column;gap:10px;align-items:center}
.player-side div{font-size:6px;color:#fff;text-align:center;font-weight:600}
.player-bar{position:absolute;left:8px;right:8px;bottom:8px;height:28px;display:flex;align-items:center;gap:10px}
.play{width:40px;height:28px;background:#222;display:flex;align-items:center;justify-content:center}
.track{position:relative;flex:1;height:8px;background:#555}
.track i{position:absolute;left:0;top:0;width:33%;height:8px;background:var(--blue)}
.track b{position:absolute;left:62px;top:-19px;background:#fff;color:#000;font-size:8px;padding:1px 3px;font-weight:600}
.hd{font-family:"Montserrat",Arial,sans-serif;font-weight:700;font-size:11px;color:var(--blue)}
.contact-row{position:absolute;top:367px;left:0;width:100%;display:flex;justify-content:center;gap:44px;font-size:14px;color:#fff;margin-left:-2px}
.contact-row div{display:flex;align-items:center;gap:9px}

/* work */
.work{top:927px;height:333px;background:var(--grey)}
.work .section-title{top:26px}
.tiles{position:absolute;left:121px;top:76px;width:954px;height:200px;display:flex;gap:3px}
.tile{flex:1;position:relative;display:flex;align-items:center;justify-content:center}
.tile:nth-child(1){background:linear-gradient(160deg,#2d3a4e,#1c2430)}
.tile:nth-child(2){background:linear-gradient(160deg,#6a5040,#2d221c)}
.tile:nth-child(3){background:linear-gradient(160deg,#4d4f52,#242526)}
.tile:nth-child(4){background:linear-gradient(160deg,#6c7362,#3a3f33)}
.pause{width:41px;height:41px;border:2px solid rgba(255,255,255,.55);border-radius:50%;display:flex;align-items:center;justify-content:center;gap:4px}
.pause i{width:4px;height:17px;border:1.5px solid rgba(255,255,255,.55);border-radius:2px}
.tile.active .pause,.tile.active .pause i{border-color:#fff}
.arrow{position:absolute;top:92px}

/* why us */
.why{top:1260px;height:536px;background:#fff}
.why .section-title{top:26px}
.feature{position:absolute;width:440px}
.feature .icon{position:absolute;left:0;top:0;width:102px;height:102px;border-radius:50%;background:#eeeeee;display:flex;align-items:center;justify-content:center}
.feature h3{position:absolute;left:121px;top:2px;font-family:"Montserrat",Arial,sans-serif;font-weight:500;font-size:16px;color:#222;text-transform:uppercase;letter-spacing:.3px}
.feature p{position:absolute;left:121px;top:30px;width:312px;font-size:12.3px;line-height:20px;color:var(--text);hyphens:auto}
.feature a{position:absolute;left:121px;top:143px;font-family:"Montserrat",Arial,sans-serif;font-weight:700;font-size:12px;color:var(--orange);text-decoration:none}

/* contact */
.contact{top:1796px;height:419px;background:var(--light)}
.contact .section-title{top:24px}
.field{position:absolute;background:#fff;border:1px solid var(--line);font-size:12px;font-style:italic;color:#aab0b5;padding:10px 28px}
.contact .btn{left:306px;top:352px;width:193px;height:37px;line-height:37px;font-size:13px}

/* footer */
.footer{top:2215px;height:188px;background:var(--dark);overflow:hidden}
.footer-panel{position:absolute;left:560px;top:0;width:700px;height:188px;background:#26262b;transform:skewX(-20deg)}
.footer .brand{left:126px;top:88px;color:#fff}
.footer h4{position:absolute;top:40px;font-family:"Montserrat",Arial,sans-serif;font-weight:500;font-size:12px;letter-spacing:.6px;color:#c9c9cc;text-transform:uppercase}
.footer-line{position:absolute;left:370px;display:flex;align-items:center;gap:17px;font-size:12.5px;font-style:italic;color:#bdbdc2}
.social{position:absolute;left:630px;top:84px;display:flex;gap:24px}
.social span{width:12px;height:12px;border-radius:50%;background:#bdbdc2}
.subscribe{position:absolute;left:843px;top:79px;width:232px;height:34px;background:#303036;border:1px solid #3d3d44;font-size:11.5px;font-style:italic;color:#9a9aa0;padding:9px 24px}
.subscribe svg{position:absolute;right:14px;top:11px}
.copyright{top:2403px;height:53px;background:var(--darker);text-align:center;line-height:53px;font-size:13px;color:#e3e3e6}
.copyright span{color:var(--orange)}
</style>
</head>
<body>

<header class="section topbar">
  <div class="brand">SkyLoftReels</div>
  <nav class="nav">
    <a class="active">Home</a><span class="sep">I</span>
    <a>services</a><span class="sep">I</span>
    <a>about us</a><span class="sep">I</span>
    <a>portfolio</a><span class="sep">I</span>
    <a>contact</a>
  </nav>
</header>

<section class="section hero">
  <div class="hero-photo" role="img" aria-label="White quadcopter drone with a camera flying against a blue sky"></div>
  <h1>SkyLoftReels</h1>
  <p>we film your home to increase your chances of sale</p>
  <div class="btn">See more</div>
  <div class="hero-tab"></div>
  <div class="dots"><span></span><span></span><span></span><span></span></div>
</section>

<section class="section how">
  <div class="how-photo" role="img" aria-label="Dark background photo of a drone resting on an asphalt road, with portfolio category thumbnails on the right"></div>
  <h2 class="section-title">How does it work?</h2>
  <div class="player" role="img" aria-label="Explainer video player showing a drone on a road">
    <div class="player-thumb"></div>
    <div class="player-title">DRONE</div>
    <div class="player-by">from <span>Northfield Studio</span></div>
    <div class="player-side">
      <div><svg width="14" height="12" viewBox="0 0 14 12"><path d="M7 11 1.5 5.5A3 3 0 0 1 7 2a3 3 0 0 1 5.5 3.5Z" fill="#fff"/></svg><br>LIKE</div>
      <div><svg width="13" height="13" viewBox="0 0 13 13"><circle cx="6.5" cy="6.5" r="5.5" fill="none" stroke="#fff" stroke-width="1.5"/><path d="M6.5 3v4h3" fill="none" stroke="#fff" stroke-width="1.5"/></svg><br>LATER</div>
      <div><svg width="13" height="13" viewBox="0 0 13 13"><path d="M1 12 11 2M6 2h5v5" fill="none" stroke="#fff" stroke-width="1.5"/></svg><br>SHARE</div>
      <div><svg width="14" height="10" viewBox="0 0 14 10"><path d="M4 1 1 5l3 4M10 1l3 4-3 4M8 1 6 9" fill="none" stroke="#fff" stroke-width="1.4"/></svg><br>EMBED</div>
    </div>
    <div class="player-bar">
      <div class="play"><svg width="12" height="14" viewBox="0 0 12 14"><path d="M0 0 12 7 0 14Z" fill="#fff"/></svg></div>
      <div class="track"><i></i><b>01:46</b></div>
      <span class="hd">IIIIII HD</span>
      <svg width="10" height="10" viewBox="0 0 10 10"><path d="M1 1l8 8M9 1 1 9" stroke="#fff" stroke-width="2"/></svg>
    </div>
  </div>
  <div class="contact-row">
    <div><svg width="26" height="26" viewBox="0 0 26 26"><circle cx="13" cy="13" r="11.5" fill="none" stroke="#fff" stroke-width="1.6"/><path d="M9 7.5c-1.5 1-1.5 3 .5 6s4 4.5 5.8 4.6c1 0 2-.8 2.2-1.4l-2.4-2-1.3.9c-1-.5-2.5-2-3-3.2l1-1.2-1.8-3.3Z" fill="#fff"/></svg>+31647208351</div>
    <div><svg width="26" height="26" viewBox="0 0 26 26"><circle cx="13" cy="13" r="11.5" fill="none" stroke="#fff" stroke-width="1.6"/><rect x="7.5" y="9" width="11" height="8" fill="none" stroke="#fff" stroke-width="1.4"/><path d="M7.5 9 13 13.5 18.5 9" fill="none" stroke="#fff" stroke-width="1.4"/></svg>contact@skyloftreels.example</div>
  </div>
</section>

<section class="section work">
  <h2 class="section-title">Our work ?</h2>
  <div class="tiles">
    <div class="tile" role="img" aria-label="Video still of a large multirotor drone against a dusk sky"><div class="pause"><i></i><i></i></div></div>
    <div class="tile active" role="img" aria-label="Video still of hands holding a small orange drone"><div class="pause"><i></i><i></i></div></div>
    <div class="tile" role="img" aria-label="Video still of a pilot handling a camera drone"><div class="pause"><i></i><i></i></div></div>
    <div class="tile" role="img" aria-label="Video still of a white camera drone on grass"><div class="pause"><i></i><i></i></div></div>
    <svg class="arrow" style="left:10px" width="10" height="16" viewBox="0 0 10 16"><path d="M8 2 2 8l6 6" fill="none" stroke="#fff" stroke-width="2.5"/></svg>
    <svg class="arrow" style="right:10px" width="10" height="16" viewBox="0 0 10 16"><path d="M2 2l6 6-6 6" fill="none" stroke="#fff" stroke-width="2"/></svg>
  </div>
</section>

<section class="section why">
  <h2 class="section-title">why us?</h2>

  <div class="feature" style="left:126px;top:100px">
    <div class="icon"><svg width="44" height="44" viewBox="0 0 44 44" fill="none" stroke="#222" stroke-width="2"><path d="M4 22 22 4h16v16L20 38Z"/><circle cx="31" cy="11" r="3"/></svg></div>
    <h3>Cheap</h3>
    <p>Lorem ipsum dolor sit amet, consectetur adipisicing elit, sed do eiusmod tempor incididunt ut labore et dolore magna aliqua. Utnim ad minim veniam, quis nostrud exercitation ulmco laboris nisi ut aliquip ex ea...</p>
    <a>READ MORE&gt;</a>
  </div>

  <div class="feature" style="left:642px;top:100px">
    <div class="icon"><svg width="44" height="44" viewBox="0 0 44 44" fill="none" stroke="#222" stroke-width="2"><circle cx="22" cy="22" r="17"/><path d="M22 11v11l7 5"/></svg></div>
    <h3>Flexible</h3>
    <p>Lorem ipsum dolor sit amet, consectetur adipisicing elit, sed do eiusmod tempor incididunt ut labore et dolore magna aliqua. Utnim ad minim veniam, quis nostrud exercitation ulmco laboris nisi ut aliquip ex ea...</p>
    <a>READ MORE&gt;</a>
  </div>

  <div class="feature" style="left:126px;top:321px">
    <div class="icon"><svg width="46" height="40" viewBox="0 0 46 40" fill="none" stroke="#222" stroke-width="2"><rect x="2" y="2" width="42" height="28"/><path d="M16 38h14M23 30v8"/><path d="M19 10v12l10-6Z" fill="#222"/></svg></div>
    <h3>4K Quality</h3>
    <p>Lorem ipsum dolor sit amet, consectetur adipisicing elit, sed do eiusmod tempor incididunt ut labore et dolore magna aliqua. Utnim ad minim veniam, quis nostrud exercitation ulmco laboris nisi ut aliquip ex ea...</p>
    <a>READ MORE&gt;</a>
  </div>

  <div class="feature" style="left:642px;top:321px">
    <div class="icon"><svg width="44" height="40" viewBox="0 0 44 40" fill="none" stroke="#222" stroke-width="2"><path d="M2 2v36h40"/><path d="M8 30l10-10 7 6 13-14"/><path d="M31 12h7v7"/></svg></div>
    <h3>Increase sale sercice</h3>
    <p>Lorem ipsum dolor sit amet, consectetur adipisicing elit, sed do eiusmod tempor incididunt ut labore et dolore magna aliqua. Utnim ad minim veniam, quis nostrud exercitation ulmco laboris nisi ut aliquip ex ea...</p>
    <a>READ MORE&gt;</a>
  </div>
</section>

<section class="section contact">
  <h2 class="section-title">Contact us</h2>
  <div class="field" style="left:306px;top:74px;width:279px;height:36px">Name</div>
  <div class="field" style="left:624px;top:74px;width:277px;height:36px">Email</div>
  <div class="field" style="left:306px;top:127px;width:279px;height:36px">Phone</div>
  <div class="field" style="left:624px;top:127px;width:277px;height:36px">Subject</div>
  <div class="field" style="left:306px;top:182px;width:595px;height:154px">Message</div>
  <div class="btn">Send message</div>
</section>

<footer class="section footer">
  <div class="footer-panel"></div>
  <div class="brand">SkyLoftReels</div>
  <h4 style="left:370px">Address of us</h4>
  <div class="footer-line" style="top:76px"><svg width="13" height="10" viewBox="0 0 13 10"><rect x=".7" y=".7" width="11.6" height="8.6" fill="none" stroke="#bdbdc2" stroke-width="1.2"/><path d="M.7.7 6.5 5.5 12.3.7" fill="none" stroke="#bdbdc2" stroke-width="1.2"/></svg>hello@skyloftreels.example</div>
  <div class="footer-line" style="top:109px"><svg width="13" height="10" viewBox="0 0 13 10"><path d="M1 4c0-2 3-3 5.5-3S12 2 12 4H9.5V3h-6v1Z M3 5h7l1.5 4h-10Z" fill="#bdbdc2"/></svg>+1 555-014-2290</div>
  <h4 style="left:630px">Follow us</h4>
  <div class="social"><span></span><span></span><span></span><span></span></div>
  <h4 style="left:843px">Subscribe</h4>
  <div class="subscribe">Enter your e-mail<svg width="6" height="10" viewBox="0 0 6 10"><path d="M1 1l4 4-4 4" fill="none" stroke="#9a9aa0" stroke-width="1.4"/></svg></div>
</footer>

<div class="section copyright">© 2015-2016 <span>SkyLoftReels</span> | All rights reserved.</div>

</body>
</html>
```